Copper Ridge Inquiries Letterhead

I would like to design a letterhead for a private investigation company. Our primary clients will be law firms. The business card is included below

```html
<!DOCTYPE html>
<html lang="en">
<head>
<meta charset="utf-8">
<title>Copper Ridge Inquiries Letterhead</title>
<link href="https://fonts.googleapis.com/css2?family=Montserrat:wght@500;600;700&family=Open+Sans:wght@400;600;700&display=swap" rel="stylesheet">
<style>
  :root {
    --navy: #1c2f5e;
    --orange: #f05a2b;
    --ink: #333333;
    --body: #7a7a7a;
    --rule: #c9c9c9;
    --backdrop: #ebebee;
    --paper: #ffffff;
    --sig-fill: #f1f1f3;
  }
  * { box-sizing: border-box; margin: 0; padding: 0; }
  html, body { width: 999px; height: 1200px; overflow: hidden; background: var(--backdrop); }
  .letterhead {
    position: absolute; left: 90px; top: 25px; width: 819px; height: 1150px;
    background: var(--paper); font-family: "Open Sans", sans-serif; color: var(--ink);
  }
  .brand {
    position: absolute; left: 59px; top: 120px; width: 160px;
    display: flex; align-items: center; gap: 8px;
  }
  .brand-dot { width: 14px; height: 14px; border-radius: 50%; background: var(--orange); flex: none; }
  .brand-name {
    font-family: "Montserrat", sans-serif; font-weight: 700; font-size: 19px; line-height: 1.1;
    color: var(--navy); letter-spacing: 0.2px;
  }
  .contact-list {
    position: absolute; right: 76px; top: 110px; list-style: none;
    font-family: "Montserrat", sans-serif; font-weight: 600; font-size: 10.5px; color: var(--navy);
  }
  .contact-list li { display: flex; justify-content: flex-end; align-items: center; gap: 6px; height: 25px; }
  .contact-icon { width: 14px; height: 14px; flex: none; }
  .header-rule { position: absolute; left: 60px; top: 253px; width: 701px; height: 1px; background: var(--rule); }
  .recipient { position: absolute; left: 66px; top: 320px; }
  .recipient-name { font-size: 24px; font-weight: 600; color: var(--navy); line-height: 1.2; }
  .recipient-title { font-size: 12px; margin-top: 2px; }
  .recipient-details { margin-top: 5px; font-size: 14px; line-height: 23px; }
  .recipient-details .key { display: inline-block; width: 27px; color: var(--orange); font-weight: 600; }
  .letter-date { position: absolute; right: 65px; top: 419px; font-size: 14px; }
  .letter-body { position: absolute; left: 65px; top: 497px; width: 688px; font-size: 14.3px; line-height: 30px; color: var(--body); }
  .letter-body p + p { margin-top: 29px; }
  .signoff { position: absolute; left: 575px; top: 845px; width: 160px; text-align: center; font-size: 14px; }
  .signature { display: block; width: 150px; height: 42px; margin: 0 auto 8px; background: var(--sig-fill); border-radius: 4px; }
  .signer-name { font-weight: 700; font-size: 15px; line-height: 18px; }
  .signer-role { line-height: 17px; }
  .footer-bands { position: absolute; left: 0; bottom: 2px; width: 100%; height: 14px; display: flex; gap: 11.4px; }
  .band { flex: 1; }
  .band--navy { background: var(--navy); }
  .band--orange { background: var(--orange); }
</style>
</head>
<body>
<main class="letterhead">
  <div class="brand">
    <span class="brand-dot"></span>
    <span class="brand-name">COPPER RIDGE INQUIRIES</span>
  </div>

  <ul class="contact-list">
    <li>210.555.0142
      <svg class="contact-icon" viewBox="0 0 14 14"><circle cx="7" cy="7" r="7" fill="var(--orange)"/><path d="M4.3 3.6c.5-.4 1-.3 1.3.2l.6 1c.2.4.1.8-.2 1l-.4.3c.3.8.9 1.5 1.8 1.9l.3-.4c.3-.3.7-.4 1-.2l1 .6c.5.3.6.9.2 1.3-.7.8-1.7 1-2.7.4C5.4 8.7 4.2 7.4 3.7 5.8c-.3-.9 0-1.700.6-2.2z" fill="#fff"/></svg>
    </li>
    <li>EL PASO, TX
      <svg class="contact-icon" viewBox="0 0 14 14"><circle cx="7" cy="7" r="7" fill="var(--orange)"/><path d="M7 3a2.6 2.6 0 0 1 2.6 2.6C9.6 7.6 7 10.8 7 10.8S4.4 7.6 4.4 5.6A2.6 2.6 0 0 1 7 3z" fill="#fff"/><circle cx="7" cy="5.6" r="1" fill="var(--orange)"/></svg>
    </li>
    <li>LICENSE NO. 04721936
      <svg class="contact-icon" viewBox="0 0 14 14"><circle cx="7" cy="7" r="7" fill="var(--orange)"/><circle cx="7" cy="5.2" r="1.8" fill="#fff"/><path d="M3.8 10.6c.3-1.8 1.6-2.8 3.2-2.8s2.9 1 3.2 2.8z" fill="#fff"/></svg>
    </li>
    <li>MORGAN@COPPERRIDGEINQUIRIES.COM
      <svg class="contact-icon" viewBox="0 0 14 14"><circle cx="7" cy="7" r="7" fill="var(--orange)"/><circle cx="7" cy="7" r="1.5" fill="none" stroke="#fff" stroke-width="1.1"/><path d="M8.5 6v1.4c0 1 1.6 1 1.6-.4A3.1 3.1 0 1 0 8.6 9.7" fill="none" stroke="#fff" stroke-width="1.1"/></svg>
    </li>
  </ul>

  <div class="header-rule"></div>

  <section class="recipient">
    <h1 class="recipient-name">Daniel Hale</h1>
    <p class="recipient-title">Chief Director</p>
    <div class="recipient-details">
      <p><span class="key">A :</span>18-4,Harbour Lane Singapore - 4410</p>
      <p><span class="key">W :</span>contact@mailbox.com, www.sitename.com</p>
      <p><span class="key">P :</span>+880 - 55501 - 2468</p>
    </div>
  </section>

  <p class="letter-date">Date, 10 September, 2019</p>

  <article class="letter-body">
    <p>This is a sample letter that has been placed to demonstrate typing remat (Your Company). letterhead design. When positioned properly, it will serve to work in harmony with all other elements letterhead. This letterhead design is meant to project an image</p>
    <p>This letterhead design is meant project an image of professionalism reliability. By using simple aligen we have created a very spacious feeling. The simplicity suggest&nbsp; rengththe spaciousnes contributes h aesthetics the layout. These basic qualities along with the (Your Company)</p>
    <p>look and helps reinforce the (Your Company) brand. letterhead design is meant to project an image p design. When positioned properly, it will serve to work in harmony all the other elements letterhead. sionalism and reliability.</p>
  </article>

  <div class="signoff">
    <span class="signature" role="img" aria-label="Handwritten signature of Owen Calder"></span>
    <p class="signer-name">Owen Calder</p>
    <p class="signer-role">Manager</p>
  </div>

  <div class="footer-bands">
    <span class="band band--navy"></span>
    <span class="band band--orange"></span>
    <span class="band band--navy"></span>
    <span class="band band--orange"></span>
    <span class="band band--navy"></span>
    <span class="band band--orange"></span>
  </div>
</main>
</body>
</html>
```